Business Card - connecting 2 souls and beggining the journey of self discovery

Logo on the front
with tag line

On the back list of services and contact details

Seminars
workshops
Coaching
podcasts

Darren Whitlow
Health & Wellbeing Life Coach
0491 372 615
darren@brightcoreliving.example
brightcoreliving.example

Industry/Entity Type

Life Coaching

Contact Information for Business Card

I like the use of colour from the logo to be used. I'm not a fan of white.

Requirements
Must have
• My tagline: The journey home starts with you
Nice to have
• Use of colour that is in the mind body soul logo

```html
<!DOCTYPE html>
<html lang="en">
<head>
<meta charset="utf-8">
<title>Brightcore Living – Business Card</title>
<link rel="stylesheet" href="https://fonts.googleapis.com/css2?family=Montserrat:wght@500;600&family=Open+Sans:wght@400;600&display=swap">
<style>
  :root {
    --stage: #2e2f31;
    --card-front: #7b7c7e;
    --card-back: #ffffff;
    --ink-grey: #6d6e70;
    --ink-white: #ffffff;
    --purple: #6a2c91;
    --green: #8cc63f;
    --orange: #f7941d;
    --yellow: #f6d32d;
    --pink: #ec4f74;
    --mark: #c9579a;
  }
  * { box-sizing: border-box; margin: 0; padding: 0; }
  html, body { width: 1200px; height: 864px; overflow: hidden; }
  body {
    background: var(--stage);
    position: relative;
    font-family: "Open Sans", sans-serif;
  }
  .card {
    position: absolute;
    width: 560px;
    height: 320px;
    border-radius: 3px;
    box-shadow: 0 10px 30px rgba(0,0,0,.45);
    overflow: hidden;
  }

  /* Front */
  .card--front {
    left: 90px; top: 90px;
    background: var(--card-front);
    display: flex; flex-direction: column; align-items: center; justify-content: center;
    color: var(--ink-white);
  }
  .brand-dot {
    width: 96px; height: 96px; border-radius: 50%;
    background: var(--mark);
  }
  .card--front .brand-name {
    margin-top: 22px;
    font-family: "Montserrat", sans-serif;
    font-weight: 600;
    font-size: 31px;
    letter-spacing: -0.5px;
  }
  .tagline {
    margin-top: 26px;
    font-size: 13px;
    letter-spacing: .3px;
  }

  /* Back */
  .card--back {
    left: 550px; top: 454px;
    background: var(--card-back);
  }
  .identity {
    position: absolute; left: 34px; top: 92px; width: 250px;
    display: flex; flex-direction: column; align-items: center;
  }
  .identity .brand-dot { width: 84px; height: 84px; }
  .identity .brand-name {
    margin-top: 14px;
    font-family: "Montserrat", sans-serif;
    font-weight: 600;
    font-size: 22px;
    letter-spacing: -0.4px;
    color: var(--ink-grey);
  }
  .divider {
    position: absolute; left: 300px; top: 78px;
    width: 2px; height: 116px; background: var(--green);
  }
  .contact {
    position: absolute; left: 322px; top: 80px;
    color: var(--ink-grey);
  }
  .person-name {
    font-family: "Montserrat", sans-serif;
    font-weight: 600; font-size: 21px; color: var(--purple);
  }
  .person-role { font-size: 13px; margin-top: 1px; }
  .contact-list { list-style: none; margin-top: 16px; font-size: 13px; line-height: 21px; }
  .contact-list li { display: flex; align-items: center; gap: 8px; }
  .contact-list svg { width: 13px; height: 13px; flex: none; }
  .services {
    position: absolute; left: 0; right: 0; bottom: 34px;
    display: flex; justify-content: center; align-items: center; gap: 10px;
    font-size: 16px; color: var(--ink-grey);
    padding-left: 110px;
  }
  .bullet { width: 5px; height: 5px; border-radius: 50%; }
  .bullet--purple { background: var(--purple); }
  .bullet--green { background: var(--green); }
  .bullet--orange { background: var(--orange); }
  .spectrum {
    position: absolute; left: 0; right: 0; bottom: 0; height: 9px;
    background: linear-gradient(90deg, var(--green) 0%, #6cc070 22%, var(--purple) 45%, var(--yellow) 68%, var(--orange) 85%, var(--pink) 100%);
  }
</style>
</head>
<body>
  <section class="card card--front" aria-label="Card front">
    <div class="brand-dot" aria-hidden="true"></div>
    <p class="brand-name">Brightcore Living</p>
    <p class="tagline">The journey home starts with you</p>
  </section>

  <section class="card card--back" aria-label="Card back">
    <div class="identity">
      <div class="brand-dot" aria-hidden="true"></div>
      <p class="brand-name">Brightcore Living</p>
    </div>
    <div class="divider"></div>
    <div class="contact">
      <p class="person-name">Darren Whitlow</p>
      <p class="person-role">Life Coach</p>
      <ul class="contact-list">
        <li>
          <svg viewBox="0 0 16 16" aria-hidden="true"><path fill="#f7941d" d="M3.6 1.5l2.2 2.8-1.3 1.6a9 9 0 0 0 5.6 5.6l1.6-1.3 2.8 2.2-1.4 2.1C7.8 14.3 1.7 8.2 1.5 2.9z"/></svg>
          0491 372 615
        </li>
        <li>
          <svg viewBox="0 0 16 16" aria-hidden="true"><rect x="1.5" y="3.5" width="13" height="9" rx="1" fill="none" stroke="#f7941d" stroke-width="1.5"/><path d="M2 4l6 5 6-5" fill="none" stroke="#f7941d" stroke-width="1.5"/></svg>
          darren@brightcoreliving.example
        </li>
        <li>
          <svg viewBox="0 0 16 16" aria-hidden="true"><g fill="none" stroke="#f7941d" stroke-width="1.3"><circle cx="8" cy="8" r="6.3"/><ellipse cx="8" cy="8" rx="2.8" ry="6.3"/><path d="M1.7 8h12.6M2.6 5h10.8M2.6 11h10.8"/></g></svg>
          brightcoreliving.example
        </li>
      </ul>
    </div>
    <div class="services">
      <span>Seminars</span><span class="bullet bullet--purple"></span>
      <span>Workshops</span><span class="bullet bullet--green"></span>
      <span>Coaching</span><span class="bullet bullet--orange"></span>
      <span>Podcasts</span>
    </div>
    <div class="spectrum"></div>
  </section>
</body>
</html>
```